Tandem Hearth Works Pty Ltd

We need business cards for a company based in Perth, we install, service and maintain fire equipment.
On the front we want a great design with our logo and a small spot for our full company name, general company email address and office number. On the back we need space for our name, title, mobile number and email address on the back.

Target Market(s)

Facility managers and commercial/industrial building owners/occupiers.

Contact Information for Business Card

Font styles to use
Sans Serif

Requirements
Must have
• Please only submit 5 of your best samples.
Darker tones are preferred.
Nice to have
• We want to use, black, red and grey. Keep it modern and clean.
I've attached the company logo and a sample of a boarder we use on our emergency plans.
Should not have
• No preference. Let the designer choose.

```html
<!DOCTYPE html>
<html lang="en">
<head>
<meta charset="utf-8">
<title>Tandem Hearth Works – Business Cards</title>
<link rel="stylesheet" href="https://fonts.googleapis.com/css2?family=Archivo:wght@400;700;800&display=swap">
<style>
  :root {
    --backdrop: #a9a9a9;
    --brand-red: #e50e1a;
    --paper: #ffffff;
    --ink: #2a2a2a;
    --rule: #8a8a8a;
  }
  html, body {
    margin: 0;
    padding: 0;
    width: 1200px;
    height: 1200px;
    overflow: hidden;
    background: var(--backdrop);
    font-family: "Archivo", sans-serif;
  }
  .sheet {
    position: relative;
    width: 1200px;
    height: 1200px;
  }
  .card {
    position: absolute;
    top: 303px;
    width: 368px;
    height: 593px;
    box-sizing: border-box;
  }
  .card--front {
    left: 200px;
    background: var(--brand-red);
    display: flex;
    align-items: center;
    justify-content: center;
  }
  .card--back {
    left: 599px;
    width: 364px;
    background: var(--paper);
    text-align: center;
  }
  .wordmark {
    margin: 0;
    font-weight: 800;
    text-transform: uppercase;
    line-height: 0.95;
    letter-spacing: -0.01em;
  }
  .card--front .wordmark {
    color: var(--paper);
    font-size: 54px;
    text-align: left;
  }
  .card--back .wordmark {
    position: absolute;
    top: 92px;
    left: 0;
    right: 0;
    color: var(--brand-red);
    font-size: 40px;
  }
  .contact {
    position: absolute;
    top: 300px;
    left: 0;
    right: 0;
  }
  .person-name {
    margin: 0;
    color: var(--brand-red);
    font-weight: 700;
    font-size: 24px;
    line-height: 1.1;
  }
  .person-title {
    margin: 2px 0 0;
    color: var(--ink);
    font-size: 19px;
  }
  .divider {
    width: 133px;
    height: 1px;
    border: 0;
    background: var(--rule);
    margin: 12px auto 10px;
  }
  .direct {
    margin: 0;
    color: var(--ink);
    font-size: 18px;
    line-height: 1.35;
  }
  .company {
    margin: 0;
    color: var(--brand-red);
    font-weight: 700;
    font-size: 22px;
    line-height: 1.2;
    text-transform: uppercase;
  }
  .office-phone {
    margin: 8px 0 0;
    color: var(--ink);
    font-weight: 700;
    font-size: 25px;
  }
  .general {
    margin: 8px 0 0;
    color: var(--ink);
    font-size: 15px;
  }
</style>
</head>
<body>
<main class="sheet">
  <section class="card card--front" aria-label="Card front">
    <p class="wordmark">Tandem<br>Hearth<br>Works</p>
  </section>

  <section class="card card--back" aria-label="Card back">
    <p class="wordmark">Tandem<br>Hearth<br>Works</p>
    <div class="contact">
      <p class="person-name">MARCUS BELLAMY</p>
      <p class="person-title">Managing Director</p>
      <hr class="divider">
      <p class="direct">555.0142.0142<br>marcus@tandemhearth.com</p>
      <hr class="divider">
      <p class="company">Tandem Hearth<br>Works Pty Ltd</p>
      <p class="office-phone">555.0190.0190</p>
      <p class="general">info@tandemhearth.com | www.tandemhearth.com</p>
    </div>
  </section>
</main>
</body>
</html>
```